Wordpress Design Project - LumaFernSites

I would like our existing old website at www.lumafernsites.example to be redesigned to a more modern attractive site using Wordpress, a total of 5 web pages. And also installed onto our new web hosting site. Please visit the existing website using Microsoft Internet explorer to see the content.
The new site must be compatible with all popular web browsers and mobile devices (if possible).
There should be a contact button available on each page with an associated form in case an interested person wants to contact us. This form must be spam proof not allowing automated crawlers from activating it.
Updates

There are only 5 pages web pages to this LumaFernSites project.

Industry/Entity Type

Internet

```html
<!DOCTYPE html>
<html lang="en">
<head>
<meta charset="utf-8">
<title>LumaFernSites</title>
<link rel="stylesheet" href="https://fonts.googleapis.com/css2?family=Open+Sans:ital,wght@0,400;0,600;0,700;1,400&display=swap">
<style>
:root{
  --blue:#0a5bb5;
  --blue-dark:#063f86;
  --blue-bright:#1170d2;
  --header-bg:#e3f1fb;
  --hero-bg:#e6e6e6;
  --panel-bg:#e3e3e3;
  --footer-bg:#e6e6e6;
  --text:#3b3b3b;
  --heading:#0b4f9c;
  --white:#ffffff;
}
*{box-sizing:border-box;margin:0;padding:0}
html,body{width:1200px;height:1056px;overflow:hidden}
body{font-family:"Open Sans",Verdana,sans-serif;color:var(--text);background:var(--white);position:relative}
.abs{position:absolute}
.site-header{left:0;top:0;width:1200px;height:78px;background:linear-gradient(#f2f9fe,var(--header-bg))}
.brand{left:155px;top:16px;display:flex;align-items:center;gap:8px}
.brand-mark{width:32px;height:32px;border-radius:50%;background:var(--blue)}
.brand-name{font-size:22px;font-weight:700;color:var(--blue-dark)}
.pill{top:21px;height:30px;border-radius:3px;background:linear-gradient(#2f78c8,#0a4f9e);border:1px solid #0a3f80;color:#fff;display:flex;align-items:center;gap:6px;padding:0 8px;font-size:14px}
.pill.phone{left:525px;width:162px;font-size:16px}
.pill.mail{left:691px;width:220px;font-size:13px}
.cta{left:915px;top:18px;width:130px;height:34px;border-radius:17px;background:linear-gradient(#1d4f7c,#062a4c);border:2px solid #2a6fb8;color:#fff;font-size:12px;font-weight:700;display:flex;align-items:center;justify-content:center}
.main-nav{left:0;top:78px;width:1200px;height:33px;background:linear-gradient(var(--blue-bright),var(--blue))}
.main-nav ul{list-style:none;position:absolute;left:142px;top:0;display:flex;height:33px}
.main-nav li{color:#fff;font-size:13px;line-height:33px;padding:0 12px;border-right:1px solid #5e98d6}
.main-nav li:last-child{border-right:none}
.search{left:890px;top:82px;width:152px;height:26px;background:#fff;border:1px solid #9bb8d8;font-size:11px;color:#466;padding:0 8px;line-height:24px}
.search-btn{right:3px;top:3px;width:19px;height:19px;border-radius:50%;background:var(--blue-bright)}
.hero{left:0;top:111px;width:1200px;height:353px;background:var(--hero-bg)}
.hero-shot{left:155px;top:123px;width:887px;height:313px;background:linear-gradient(100deg,#c9a989 0%,#e8d8c8 30%,#bfa893 55%,#7b6a60 80%,#a89a92 100%);box-shadow:0 18px 18px -12px rgba(0,0,0,.45)}
.hero-title{left:177px;top:378px;font-size:31px;font-style:italic;color:#fff;text-shadow:0 1px 3px rgba(0,0,0,.4)}
.dots{left:155px;top:239px;width:35px;height:82px;background:#e8e8e8;border-radius:0 4px 4px 0;display:flex;flex-direction:column;align-items:center;justify-content:center;gap:5px}
.dots i{width:8px;height:8px;border-radius:50%;background:#444;display:block}
.dots i.on{background:var(--blue-bright)}
.welcome{left:155px;top:479px;width:592px;height:210px;background:linear-gradient(135deg,var(--blue-dark),var(--blue) 60%,#1565c0);color:#fff}
.welcome h2{position:absolute;left:21px;top:19px;font-size:18px;font-style:italic;font-weight:400}
.welcome hr{position:absolute;left:21px;top:46px;width:560px;border:0;border-top:1px solid #3b86d6}
.welcome .copy{position:absolute;left:21px;top:63px;width:353px;font-size:11px;line-height:16.6px;text-align:justify}
.welcome .copy p+p{margin-top:11px}
.welcome-photo{left:385px;top:67px;width:180px;height:120px;background:linear-gradient(90deg,#e8e4de,#c9a68a 60%,#6b4a32)}
.why{left:155px;top:709px;width:390px}
.why h2{font-size:20px;font-weight:400;color:var(--heading)}
.why p{margin-top:14px;font-size:13px;line-height:20.3px;text-align:justify}
.why p+p{margin-top:16px}
.phone-photo{left:558px;top:730px;width:170px;height:200px;background:linear-gradient(#3a3d42,#8b9097 60%,#c8ccd0);border-radius:6px}
.panel{left:759px;width:280px;background:var(--panel-bg)}
.panel h3{height:34px;background:var(--blue-bright);color:#fff;font-weight:400;font-size:16px;line-height:34px;padding-left:10px}
.field{position:absolute;background:#fff;border:1px solid #cfcfcf;font-size:10px;color:#444;padding-left:10px}
.quick{top:480px;height:287px}
.captcha{left:18px;top:215px;width:155px;height:60px;background:linear-gradient(#f4f0ea,#b01c1c 70%);border:2px solid #b01c1c;border-radius:2px}
.btn{position:absolute;background:var(--blue-bright);color:#fff;font-size:12px;font-weight:600;text-align:center}
.news{top:784px;height:181px}
.site-footer{left:0;top:965px;width:1200px;height:91px;background:var(--footer-bg)}
.follow{left:156px;top:30px;font-size:12px;font-weight:700;color:var(--heading);display:flex;align-items:center;gap:9px}
.follow span{width:22px;height:22px;background:var(--blue-bright);display:block;border-radius:2px;margin-left:3px}
.follow span.rss{background:#f08a1c}
.foot-links{right:160px;top:24px;font-size:11px;color:#444;text-align:right;line-height:20px}
.foot-links b{font-weight:400;margin:0 9px}
</style>
</head>
<body>
<header class="site-header abs">
  <div class="brand abs"><span class="brand-mark"></span><span class="brand-name">LumaFernSites</span></div>
  <div class="pill phone abs">
    <svg width="18" height="14" viewBox="0 0 18 14"><path d="M1 5c0-3 16-3 16 0l-3 1-1-2H5L4 6zM4 7h10l2 6H2z" fill="#fff"/></svg>1.888.555.0142</div>
  <div class="pill mail abs">
    <svg width="18" height="13" viewBox="0 0 18 13"><rect x="1" y="1" width="16" height="11" fill="none" stroke="#fff" stroke-width="1.5"/><path d="M1 1l8 6 8-6" fill="none" stroke="#fff" stroke-width="1.5"/></svg>info@lumafernsites.example</div>
  <div class="cta abs">CONTACT US</div>
</header>
<nav class="main-nav abs">
  <ul>
    <li>LumaFernSites Home</li>
    <li>Telephone VoIP&nbsp; Solution</li>
    <li>IP, LAN and Internet</li>
    <li>Support Services</li>
    <li>Contact Us</li>
  </ul>
</nav>
<div class="search abs">Search<span class="search-btn abs"></span></div>
<section class="hero abs"></section>
<div class="hero-shot abs" role="img" aria-label="Photograph of a support team wearing headsets"></div>
<div class="dots abs"><i></i><i></i><i class="on"></i><i></i><i></i></div>
<div class="hero-title abs">Support Services</div>

<section class="welcome abs">
  <h2>Welcometo Our Site</h2>
  <hr>
  <div class="copy">
    <p>LumaFernSites provides complete telephone VoIP PBX solutions for businesses large and small.</p>
    <p>Our team of telecom engineers will design and install the best business telephone VoIP PBX solution for your requirements.&nbsp; System features include: standard and advanced PBX call control actions, video telephone calling, toll free calling any where in the world, and 24x7 support.</p>
  </div>
  <div class="welcome-photo abs" role="img" aria-label="Photograph of a support agent with a headset"></div>
</section>

<section class="why abs">
  <h2>Why LumaFernSites?</h2>
  <p>LumaFernSites provides state of the art VoIP PBX phone solutions with products tailored to small, medium, and large businesses. Our engineering team will asses your communication requirements and provide you with the best designed solution for your business needs.</p>
  <p>LumaFernSites will be there for you during the whole process. From the initial quote all the way through installation and support. LumaFernSites is committed to you!</p>
</section>
<div class="phone-photo abs" role="img" aria-label="Photograph of a desk video phone"></div>

<aside class="panel quick abs">
  <h3>Quick Contact</h3>
  <div class="field" style="left:18px;top:54px;width:269px;height:28px;width:269px;line-height:26px;width:269px"></div>
</aside>
<aside class="panel quick abs" style="background:transparent">
  <div class="field" style="left:18px;top:50px;width:251px;height:28px;line-height:26px">Enter the Name</div>
  <div class="field" style="left:18px;top:85px;width:251px;height:28px;line-height:26px">Enter the Ph No</div>
  <div class="field" style="left:18px;top:118px;width:251px;height:86px;padding-top:7px">Message</div>
  <div class="captcha abs" role="img" aria-label="Spam protection word challenge"></div>
  <div class="btn" style="left:192px;top:244px;width:70px;height:28px;line-height:28px">Submit</div>
</aside>

<aside class="panel news abs">
  <h3>Newsletter Signup</h3>
  <div class="field" style="left:23px;top:57px;width:232px;height:32px;line-height:30px;font-size:11px">Enter the Name</div>
  <div class="field" style="left:23px;top:101px;width:232px;height:32px;line-height:30px;font-size:11px">Enter the E mail id</div>
  <div class="btn" style="left:184px;top:142px;width:70px;height:28px;line-height:28px">Subscribe</div>
</aside>

<footer class="site-footer abs">
  <div class="follow abs">Follow Us On <span></span><span></span><span></span><span class="rss"></span></div>
  <div class="foot-links abs">
    LumaFernSites Home<b>/</b>Telephone VoIP&nbsp; Solution<b>/</b>IP, LAN and Internet<b>/</b>Support Services<b>/</b>Contact Us<br>
    Copyrights @ 2013 All Rights Reserved
  </div>
</footer>
</body>
</html>
```